birchwell hollow cattle company website

we would like a home page, an about us page, a page for sires, a page for dams, A sale page where we can list progreny for sale and a contact us. on the about us page we would like there to be a family picture. on the sires page we would like to have a picture of each sire, a description beside them and a link to their online profile at northern hereford registry. on the dam page we would like to have a picture of each dam, aswell as a description beside them aswell as a link to the northern hereford registry site. would like the website to very mobile phone friendly as expecting most traffic to be on phone. we would like the website to look and feel very mich like a farm, rustic, barbed wire and other farm feels. we would also like a frozen genetics pages where we can include pictures and descriptions of the sires and dams aswell as a price for embryos and semen. we need to website to be easy to maintain so we can update pictures and information as it changes, we would like there to be a feature so that people can sign up to be on our mailing list by giving us their mailing addess and email and full name
aswell as an area where they can send us a message to contact us.

leaving for work for 3 weeks in the canadian arctic will have limited ability to use the internet

Target Market(s)

other ranchers, farmers, cattlemen,

Industry/Entity Type

farming, agriculture, cattle

Coding

Coded - Design and coding required

Requirements
Must have
• about page, contact page, sires page, dams page, SALE page.
Nice to have
• country/farm vibe, barbed wire, wood,

```html
<!DOCTYPE html>
<html lang="en">
<head>
<meta charset="utf-8">
<title>Birchwell Hollow Cattle Company</title>
<link href="https://fonts.googleapis.com/css2?family=Oswald:wght@500;600;700&family=Roboto:wght@400;500;700&display=swap" rel="stylesheet">
<style>
:root{
  --backdrop:#d9c9b9;
  --bark:#1c0c06;
  --bark-deep:#2a1209;
  --card:#4a2a1e;
  --soil:#050302;
  --gold:#d4a83a;
  --rust:#7a2a0c;
  --rust-text:#8a3a14;
  --ink:#1a1a1a;
  --cream:#f3ece2;
  --muted:#9a928a;
  --line:#6a625c;
}
*{box-sizing:border-box;margin:0;padding:0}
html,body{width:1200px;height:2329px;overflow:hidden}
body{background:var(--backdrop);font-family:"Roboto",Arial,sans-serif;color:var(--cream);position:relative}
.page{position:absolute;left:81px;top:81px;width:1038px;height:2168px;background:var(--bark);overflow:hidden;box-shadow:0 10px 30px rgba(60,30,10,.25)}
.heading{font-family:"Oswald",Impact,sans-serif;font-weight:600}

/* header */
.brand-box{position:absolute;left:43px;top:0;width:119px;height:101px;background:var(--bark-deep);clip-path:polygon(0 0,100% 0,100% 82%,50% 100%,0 82%);z-index:3;display:flex;flex-direction:column;align-items:center;justify-content:center;padding-bottom:12px}
.brand-box span{font-family:"Oswald",sans-serif;font-weight:600;color:#fff;font-size:13px;line-height:1.1;text-align:center;letter-spacing:.3px}
.nav{position:absolute;top:13px;right:14px;display:flex;align-items:center;z-index:3}
.nav a{font-family:"Oswald",sans-serif;font-weight:600;font-size:9.5px;color:#1a1a1a;text-decoration:none;margin-right:24px;letter-spacing:.2px}
.nav a.active{color:var(--rust-text)}
.nav .cta{display:flex;height:22px;margin-left:2px}
.nav .cta a{margin:0;display:flex;align-items:center;padding:0 10px;font-size:9.5px;border:1px solid var(--rust)}
.nav .cta .sale{background:var(--rust);color:#fff}
.nav .cta .contact{color:var(--rust-text);background:rgba(255,255,255,.3)}

/* hero */
.hero{position:absolute;left:0;top:0;width:1038px;height:560px;background:linear-gradient(180deg,#f4f6f7 0%,#d5dce0 18%,#a9b3ba 34%,#8a5a3c 52%,#7a4528 66%,#8e6a4a 82%,#cbb47e 94%)}
.hero-shade{position:absolute;inset:0;background:radial-gradient(ellipse 260px 150px at 519px 330px,rgba(30,12,4,.35),rgba(30,12,4,0))}
.hero-copy{position:absolute;left:0;right:0;top:244px;text-align:center;color:#fff}
.eyebrow{font-family:"Roboto",sans-serif;font-weight:700;font-size:10px;letter-spacing:2.6px}
.hero h1{font-size:44px;line-height:46px;margin-top:4px;font-weight:600}
.hero p{font-size:10.5px;line-height:15px;width:360px;margin:9px auto 0}
.hero .buttons{margin-top:10px;display:flex;justify-content:center;gap:5px}
.pill{display:inline-flex;align-items:center;height:23px;padding:0 13px;border-radius:12px;background:#fff;color:#1a1a1a;font-weight:500;font-size:10.5px;text-decoration:none}
.grass-edge{position:absolute;left:0;top:520px;width:1038px;height:60px}

/* herd */
.herd{position:absolute;top:650px;left:0;right:0;text-align:center}
.herd h2{color:var(--gold);font-size:43px;line-height:46px}
.herd .lede{font-size:13px;line-height:19px;width:380px;margin:10px auto 0;color:#f1e9df}
.cards{position:absolute;top:764px;left:76px;display:flex;gap:26px}
.card{width:202px;height:255px;background:var(--card);position:relative;text-align:center}
.card .photo{height:135px;width:100%}
.card .arc{position:absolute;left:0;top:112px;width:202px;height:30px}
.card h3{position:absolute;top:135px;left:0;right:0;font-size:20px;color:#fff;letter-spacing:.3px}
.card p{position:absolute;top:168px;left:20px;right:20px;font-size:10.2px;line-height:15px;color:#e9ddd0}
.card .btn{position:absolute;top:210px;left:50%;transform:translateX(-50%);height:23px;padding:0 17px;border-radius:12px;background:var(--gold);color:#2a1209;font-weight:700;font-size:10px;display:flex;align-items:center;white-space:nowrap}
.photo.sire{background:linear-gradient(180deg,#c9d2d8 0%,#9aa4a9 35%,#7a3f1f 60%,#8e5230 100%)}
.photo.dam{background:linear-gradient(180deg,#d8dde0 0%,#a7aeb1 30%,#2a2522 55%,#3a3430 100%)}
.photo.frozen{background:linear-gradient(180deg,#e2e6e8 0%,#aab4bb 45%,#8d98a0 75%,#d9dee1 100%)}
.photo.calves{background:linear-gradient(180deg,#dfe3e5 0%,#b8bfc2 30%,#2b2725 60%,#3d3833 100%)}

/* about */
.family-photo{position:absolute;left:100px;top:1107px;width:330px;height:330px;border-radius:50%;background:linear-gradient(160deg,#8a6444 0%,#5e3f28 40%,#7d5c44 70%,#4a3a30 100%)}
.seal{position:absolute;left:354px;top:1141px;width:136px;height:136px;border-radius:50%;background:radial-gradient(circle,#2a2623 58%,#c9a23e 60%,#e3c469 70%,#9a7420 100%)}
.about{position:absolute;left:538px;top:1153px;width:380px}
.about h2{font-size:36px;line-height:40px;color:#fff;font-weight:700}
.about h3{font-size:21px;line-height:28px;color:#fff;margin-top:6px;font-weight:600}
.about p{font-size:10.5px;line-height:17.3px;color:#eee3d6;margin-top:13px}
.about .btn{display:inline-flex;align-items:center;margin-top:10px;height:23px;padding:0 13px;border-radius:12px;background:var(--gold);color:#2a1209;font-weight:700;font-size:10.5px}

/* forms */
.soil{position:absolute;left:0;top:1490px;width:1038px;height:678px;background:var(--soil)}
.soil-edge{position:absolute;left:0;top:0;width:1038px;height:50px}
.form-col{position:absolute;top:1607px;width:389px;text-align:center}
.form-col.mail{left:82px}
.form-col.quick{left:566px}
.form-col h2{font-size:40px;line-height:46px;color:#fff;font-weight:600}
.form-col .sub{font-family:"Oswald",sans-serif;font-weight:600;font-size:20.5px;line-height:28px;color:#fff;margin-top:4px}
.fields{margin-top:22px;display:flex;flex-wrap:wrap;gap:0 11px}
.field{height:43px;border-bottom:1px solid var(--line);display:flex;align-items:flex-end;padding:0 11px 8px;font-size:10px;color:var(--muted);text-align:left}
.field.half{width:189px}
.field.full{width:389px}
.submit{margin-top:28px;height:28px;border-radius:14px;background:var(--gold);color:#1a1a1a;font-weight:700;font-size:10px;display:flex;align-items:center;justify-content:center}
.tip{font-size:8px;color:#9c958e;margin-top:14px}
.note{position:absolute;top:1920px;left:0;right:0;text-align:center;font-size:8px;color:#9c958e}

/* footer */
.divider{position:absolute;top:1977px;left:0;width:1038px;height:1px;background:#2a2420}
.footer-brand{position:absolute;top:2035px;left:0;right:0;text-align:center;font-family:"Oswald",sans-serif;font-weight:600;font-size:15px;line-height:17px;color:#fff}
.footer-nav{position:absolute;top:2100px;left:0;right:0;display:flex;justify-content:center;gap:20px}
.footer-nav a{font-family:"Oswald",sans-serif;font-weight:600;font-size:9.5px;color:#fff;text-decoration:none}
.copyright{position:absolute;top:2132px;left:0;right:0;text-align:center;font-size:10px;color:#fff}
</style>
</head>
<body>
<div class="page">

  <section class="hero">
    <div class="hero" role="img" aria-label="Photo of a red Hereford bull standing on straw in front of steel corral panels on a snowy ranch"></div>
    <div class="hero-shade"></div>
    <div class="hero-copy">
      <div class="eyebrow">RANCH-READY • NORTHERN HEREFORD REGISTRY</div>
      <h1 class="heading">Rustic cattle breeding,<br>built for real work.</h1>
      <p>Birchwell Hollow Cattle Company raises quality genetics with a focus on sound structure, easy-doing cattle, and ranch practicality. Explore our sires, dams, and frozen genetics — or view current lots for sale.</p>
      <div class="buttons">
        <a class="pill" href="#">View For Sale</a>
        <a class="pill" href="#">Frozen Genetics</a>
        <a class="pill" href="#">Meet the Family</a>
      </div>
    </div>
    <svg class="grass-edge" viewBox="0 0 1038 60" preserveAspectRatio="none" aria-hidden="true">
      <path fill="#1c0c06" d="M0 28 L20 22 L38 30 L60 20 L82 29 L104 21 L126 31 L150 23 L172 30 L196 19 L220 28 L244 22 L268 32 L292 21 L316 29 L340 24 L364 31 L388 20 L412 28 L436 23 L460 33 L484 22 L508 29 L532 24 L556 31 L580 21 L604 28 L628 23 L652 32 L676 22 L700 29 L724 24 L748 31 L772 20 L796 28 L820 22 L844 30 L868 21 L892 29 L916 23 L940 31 L964 20 L988 28 L1012 22 L1038 30 L1038 60 L0 60 Z"/>
    </svg>
  </section>

  <header>
    <div class="brand-box"><span>BIRCHWELL HOLLOW<br>CATTLE COMPANY</span></div>
    <nav class="nav">
      <a class="active" href="#">HOME</a>
      <a href="#">ABOUT</a>
      <a href="#">SIRES</a>
      <a href="#">DAMS</a>
      <a href="#">FROZEN GENETICS</a>
      <a href="#">FOR SALE</a>
      <div class="cta">
        <a class="sale" href="#">VIEW SALE LOTS</a>
        <a class="contact" href="#">CONTACT US</a>
      </div>
    </nav>
  </header>

  <section class="herd">
    <h2 class="heading">Explore the herd</h2>
    <p class="lede">A clean layout that feels rustic — wood tones, subtle barbed wire texture, and easy scrolling on phone.</p>
  </section>

  <div class="cards">
    <article class="card">
      <div class="photo sire" role="img" aria-label="Photo of a red bull beside corral panels"></div>
      <svg class="arc" viewBox="0 0 202 30" aria-hidden="true"><path d="M0 30 Q101 -8 202 30 Z" fill="#4a2a1e"/><path d="M0 30 Q101 -8 202 30" fill="none" stroke="#d4a83a" stroke-width="2"/></svg>
      <h3 class="heading">OUR SIRES</h3>
      <p>Browse our premium Angus bulls (or each property)</p>
      <span class="btn">VIEW SIRES</span>
    </article>
    <article class="card">
      <div class="photo dam" role="img" aria-label="Photo of a black cow in a snowy pen"></div>
      <svg class="arc" viewBox="0 0 202 30" aria-hidden="true"><path d="M0 30 Q101 -8 202 30 Z" fill="#4a2a1e"/><path d="M0 30 Q101 -8 202 30" fill="none" stroke="#d4a83a" stroke-width="2"/></svg>
      <h3 class="heading">OUR DAMS</h3>
      <p>Browse our elite Angus Females (lots)</p>
      <span class="btn">VIEW DAMS</span>
    </article>
    <article class="card">
      <div class="photo frozen" role="img" aria-label="Photo of two steel semen storage tanks with cold vapour"></div>
      <svg class="arc" viewBox="0 0 202 30" aria-hidden="true"><path d="M0 30 Q101 -8 202 30 Z" fill="#4a2a1e"/><path d="M0 30 Q101 -8 202 30" fill="none" stroke="#d4a83a" stroke-width="2"/></svg>
      <h3 class="heading">FROZEN GENETICS</h3>
      <p>Discover our frozen embryos and semen within reach.</p>
      <span class="btn">FROZEN GENETICS</span>
    </article>
    <article class="card">
      <div class="photo calves" role="img" aria-label="Photo of two black calves with ear tags in the snow"></div>
      <svg class="arc" viewBox="0 0 202 30" aria-hidden="true"><path d="M0 30 Q101 -8 202 30 Z" fill="#4a2a1e"/><path d="M0 30 Q101 -8 202 30" fill="none" stroke="#d4a83a" stroke-width="2"/></svg>
      <h3 class="heading">CALVES</h3>
      <p>Check out our ranch-remetic progeny for sale.</p>
      <span class="btn">VIEW PROGENY</span>
    </article>
  </div>

  <div class="family-photo" role="img" aria-label="Family photo of the ranch family with their dog in front of a wooden barn door"></div>
  <div class="seal" aria-hidden="true"></div>
  <section class="about">
    <h2 class="heading">ABOUT US</h2>
    <h3 class="heading">Welcome to Birchwell Hollow<br>Cattle Company!</h3>
    <p>We are a small family-owned cattle company rooted on the prairie. We specialize in sound feet and easy-doing cows. Through long winters and busy calving seasons we keep building great cattle that ranchers choose to make their herds better.</p>
    <span class="btn">LEARN MORE</span>
  </section>

  <div class="soil">
    <svg class="soil-edge" viewBox="0 0 1038 50" preserveAspectRatio="none" aria-hidden="true">
      <rect width="1038" height="50" fill="#1c0c06"/>
      <path fill="#050302" d="M0 6 L14 14 L26 4 L40 12 L54 2 L70 13 L86 5 L102 15 L118 3 L134 12 L150 6 L168 16 L186 4 L204 13 L222 7 L240 16 L258 5 L276 14 L294 6 L312 15 L330 3 L348 13 L366 7 L384 16 L402 4 L420 13 L438 8 L456 17 L474 5 L492 14 L510 7 L528 16 L546 4 L564 13 L582 6 L600 15 L618 3 L636 12 L654 7 L672 16 L690 5 L708 14 L726 6 L744 15 L762 4 L780 13 L798 8 L816 17 L834 5 L852 14 L870 7 L888 16 L906 4 L924 13 L942 6 L960 15 L978 3 L996 12 L1014 6 L1038 14 L1038 50 L0 50 Z"/>
    </svg>
  </div>

  <section class="form-col mail">
    <h2 class="heading">Mailing list</h2>
    <div class="sub">Let ranchers sign up with full name,<br>email, and mailing address.</div>
    <div class="fields">
      <div class="field half">Full Name</div>
      <div class="field half">Email Address</div>
      <div class="field full">Mailing Address</div>
    </div>
    <div class="submit">JOIN THE MAILING LIST</div>
    <div class="tip">Tip: In PressKit, connect this form to your email platform so subscribers are saved automatically.</div>
  </section>

  <section class="form-col quick">
    <h2 class="heading">Quick contact</h2>
    <div class="sub">Give visitors a simple message form so they<br>can reach out fast from mobile.</div>
    <div class="fields">
      <div class="field half">Full Name</div>
      <div class="field half">Email Address</div>
      <div class="field full">Message</div>
    </div>
    <div class="submit">SEND MESSAGE</div>
    <div class="tip">Tip: Use FormHand / FieldPost / Mailrail to receive messages by email.</div>
  </section>

  <p class="note">Want a stronger “farm feel”? Swap the hero photo for a barn/wood scene and keep the subtle wire texture. This layout stays clean and premium (contest-friendly) while still rustic.</p>

  <footer>
    <div class="divider"></div>
    <div class="footer-brand">BIRCHWELL HOLLOW<br>CATTLE COMPANY</div>
    <nav class="footer-nav">
      <a href="#">HOME</a><a href="#">ABOUT</a><a href="#">SIRES</a><a href="#">DAMS</a><a href="#">FROZEN GENETICS</a><a href="#">FOR SALE</a><a href="#">CONTACT</a>
    </nav>
    <div class="copyright">© 2026 Birchwell Hollow Cattle Company. All rights reserved.</div>
  </footer>

</div>
</body>
</html>
```